Zolvana Stationary and Branding Documents

Corporate Identity Branding stationary needed for IT Recruiting Firm.

I already have a Logo, business cards and website. I need to get designs completed for the remaining corporate identity documents.

The documentation should use similar colors as my website and business card. The designs should modern and clean.

http://zolvanaworks.example/

Target Market(s)

Information Technology Industry

Industry/Entity Type

Information Technology

Colors
3377b5
0255a3
fbee3e
f78f20
f37122
33a6d7
000000
0592cd

Requirements
Must have
• Letter Head
• Folder Design
• PowerPoint Design
• Invoice
• Envelope
Nice to have
• Proposal
• Flyer
• Brochure
Should not have
• Logo
• Business Cards
• Website

```html
<!DOCTYPE html>
<html lang="en">
<head>
<meta charset="utf-8">
<title>Zolvana Letterhead</title>
<link rel="stylesheet" href="https://fonts.googleapis.com/css2?family=Open+Sans:wght@400;600&display=swap">
<style>
  :root {
    --backdrop: #d9dadc;
    --paper: #f7f7f7;
    --brand-blue: #0255a3;
    --text-dark: #333333;
    --watermark: #dbe3eb;
  }
  * { margin: 0; padding: 0; box-sizing: border-box; }
  html, body {
    width: 1066px;
    height: 1200px;
    overflow: hidden;
    background: var(--backdrop);
    font-family: "Open Sans", Arial, sans-serif;
  }
  .letterhead {
    position: absolute;
    left: 109px;
    top: 0;
    width: 848px;
    height: 1200px;
    background: var(--paper);
    overflow: hidden;
  }
  .letterhead__header {
    position: absolute;
    top: 78px;
    left: 72px;
    right: 60px;
    display: flex;
    justify-content: space-between;
    align-items: flex-start;
  }
  .brand-name {
    font-size: 50px;
    font-weight: 400;
    color: var(--brand-blue);
    line-height: 1;
  }
  .contact {
    display: flex;
    gap: 22px;
    margin-top: 18px;
    font-size: 12.5px;
    font-weight: 400;
    line-height: 1.45;
    color: var(--text-dark);
  }
  .contact__address { font-style: normal; }
  .contact__line {
    display: flex;
    align-items: center;
    gap: 8px;
  }
  .contact__icon {
    width: 11px;
    height: 11px;
    flex: none;
  }
  .letterhead__watermark {
    position: absolute;
    left: 0;
    right: 0;
    bottom: 30px;
    text-align: center;
    font-size: 190px;
    font-weight: 400;
    color: var(--watermark);
    line-height: 1;
    white-space: nowrap;
  }
</style>
</head>
<body>
  <main class="letterhead">
    <header class="letterhead__header">
      <div class="brand-name">Zolvana</div>
      <div class="contact">
        <address class="contact__address">
          One Harbor Plaza<br>410 Cedar Avenue NW
        </address>
        <div class="contact__details">
          <div class="contact__line">
            <svg class="contact__icon" viewBox="0 0 24 24" aria-hidden="true"><path fill="#0255a3" d="M6.6 10.8a15.1 15.1 0 0 0 6.6 6.6l2.2-2.2c.3-.3.7-.4 1-.2 1.1.4 2.3.6 3.6.6.6 0 1 .4 1 1V20c0 .6-.4 1-1 1C10.6 21 3 13.4 3 4c0-.6.4-1 1-1h3.5c.6 0 1 .4 1 1 0 1.300.2 2.500.6 3.600.1.300 0 .700-.2 1z"/></svg>
            <span>8005550137</span>
          </div>
          <div class="contact__line">
            <svg class="contact__icon" viewBox="0 0 24 24" aria-hidden="true"><path fill="#0255a3" d="M3 5h18a1 1 0 0 1 1 1v12a1 1 0 0 1-1 1H3a1 1 0 0 1-1-1V6a1 1 0 0 1 1-1zm1 2v.4l8 5 8-5V7l-8 5z"/></svg>
            <span>info@zolvanaworks.example</span>
          </div>
        </div>
      </div>
    </header>
    <div class="letterhead__watermark" aria-hidden="true">Zolvana</div>
  </main>
</body>
</html>
```